Quillmarsh Property Solutions need a business card design

Hello guys. We would need a business card design asap please.
We are a start up property investment business based in London UK specialised in buying, selling, managing and letting properties and helping distressed property owners.
The name of our Business is Quillmarsh, the logo symbolises the four fundamental elements of the world (earth, air, fire and water) and so it stands for strength, stability, longevity.
We would like the business card to communicate professionalism and reliability. Many many thanks indeed for your work.

Details:

1.) Rosalind Updike
Property Investor
Mobile: +44(0)7700123456
Email: rosalind.quillmarsh@mailbox-example.com

2.) Dominic Updike
Property Investor
Mobile: +44(0)7700987654
Email: dominic.quillmarsh@mailbox-example.com

```html
<!DOCTYPE html>
<html lang="en">
<head>
<meta charset="utf-8">
<title>Quillmarsh Property Solutions – Business Card</title>
<link rel="stylesheet" href="https://fonts.googleapis.com/css2?family=Open+Sans:wght@400;600;700;800&display=swap">
<style>
  :root {
    --canvas-bg: #4a4541;
    --card-white: #ffffff;
    --card-grey: #e6e7e9;
    --ink: #2b2b2b;
    --ink-soft: #444444;
    --accent-blue: #3a8ee6;
    --icon-white: #ffffff;
  }
  * { box-sizing: border-box; margin: 0; padding: 0; }
  html, body {
    width: 1200px; height: 897px; overflow: hidden;
    background: var(--canvas-bg);
    font-family: "Open Sans", Arial, sans-serif;
  }
  .canvas { position: relative; width: 1200px; height: 897px; }

  .card {
    position: absolute;
    width: 540px; height: 310px;
    border-radius: 34px;
    box-shadow: 0 14px 30px rgba(0,0,0,0.35);
  }

  /* Back side: contact details */
  .card-back { left: 70px; top: 100px; background: var(--card-white); }
  .holder { position: absolute; left: 44px; bottom: 58px; color: var(--ink); }
  .holder-name { font-size: 17px; letter-spacing: 0.3px; text-transform: uppercase; }
  .holder-name .first { font-weight: 800; }
  .holder-name .last { font-weight: 400; }
  .holder-title { font-size: 9.5px; text-transform: uppercase; margin-top: 2px; color: var(--ink-soft); letter-spacing: 0.2px; }

  .contacts {
    position: absolute; right: 28px; top: 46px;
    display: grid; grid-template-columns: auto auto; column-gap: 20px; row-gap: 26px;
  }
  .contact { display: flex; align-items: center; gap: 9px; }
  .contact-icon {
    width: 24px; height: 24px; border-radius: 5px; flex: none;
    background: var(--accent-blue);
    display: flex; align-items: center; justify-content: center;
  }
  .contact-lines { font-size: 9.5px; line-height: 13px; color: var(--ink-soft); text-transform: uppercase; white-space: nowrap; }

  /* Front side: company name */
  .card-front { left: 590px; top: 487px; background: var(--card-grey); }
  .brand {
    position: absolute; inset: 0;
    display: flex; align-items: center; justify-content: center; gap: 16px;
  }
  .brand-dot { width: 46px; height: 46px; border-radius: 50%; background: var(--accent-blue); }
  .brand-text { color: var(--ink); font-weight: 700; text-transform: uppercase; }
  .brand-name { font-size: 26px; letter-spacing: 1px; line-height: 1; }
  .brand-tagline { font-size: 10.5px; letter-spacing: 1.2px; margin-top: 5px; }
</style>
</head>
<body>
<main class="canvas">

  <section class="card card-back" aria-label="Business card back">
    <div class="contacts">
      <div class="contact">
        <span class="contact-icon">
          <svg width="13" height="13" viewBox="0 0 24 24"><path fill="var(--icon-white)" d="M6.6 10.8c1.4 2.8 3.8 5.1 6.6 6.6l2.2-2.2c.3-.3.7-.4 1-.2 1.1.4 2.3.6 3.6.6.6 0 1 .4 1 1V20c0 .6-.4 1-1 1C10.6 21 3 13.4 3 4c0-.6.4-1 1-1h3.5c.6 0 1 .4 1 1 0 1.3.2 2.5.6 3.6.1.3 0 .7-.2 1L6.6 10.8z"/></svg>
        </span>
        <div class="contact-lines">Mobile<br>+44(0)7700123456</div>
      </div>
      <div class="contact">
        <span class="contact-icon">
          <svg width="14" height="14" viewBox="0 0 24 24" fill="none" stroke="var(--icon-white)" stroke-width="1.8"><circle cx="12" cy="12" r="9"/><ellipse cx="12" cy="12" rx="4" ry="9"/><path d="M3 12h18M5 7h14M5 17h14"/></svg>
        </span>
        <div class="contact-lines">www.quillmarsh-example.com<br>quillmarsh-example.com</div>
      </div>
      <div class="contact">
        <span class="contact-icon">
          <svg width="14" height="14" viewBox="0 0 24 24" fill="none" stroke="var(--icon-white)" stroke-width="1.8"><rect x="3" y="5" width="18" height="14" rx="1.5"/><path d="M3 6l9 7 9-7"/></svg>
        </span>
        <div class="contact-lines">Email<br>rosalind.quillmarsh@mailbox-example.com</div>
      </div>
      <div class="contact">
        <span class="contact-icon">
          <svg width="13" height="13" viewBox="0 0 24 24"><path fill="var(--icon-white)" d="M12 2C8.1 2 5 5.1 5 9c0 5.2 7 13 7 13s7-7.8 7-13c0-3.9-3.1-7-7-7zm0 9.5c-1.4 0-2.5-1.1-2.5-2.5S10.6 6.5 12 6.5s2.5 1.1 2.5 2.5-1.1 2.5-2.5 2.5z"/></svg>
        </span>
        <div class="contact-lines">London<br>United Kingdom</div>
      </div>
    </div>

    <div class="holder">
      <p class="holder-name"><span class="first">Rosalind</span> <span class="last">Updike</span></p>
      <p class="holder-title">Property Investor</p>
    </div>
  </section>

  <section class="card card-front" aria-label="Business card front">
    <div class="brand">
      <span class="brand-dot"></span>
      <div class="brand-text">
        <p class="brand-name">Quillmarsh</p>
        <p class="brand-tagline">Property Solutions</p>
      </div>
    </div>
  </section>

</main>
</body>
</html>
```